New Corporate Email footer (business card design) for 40th Anniversary for Timber Traders

We are traders in sustainable timber worldwide, specialising in tropical hardwoods.
We need to keep our current company logo, but update our email footer with a business card like design which marks the company's 40th Anniversary. 1981-2021. We would need:
Company Logo, Name and Address, website
Sender's: Name, Tel no, fax no, email address
We would need this in a format which we could update ourselves re names/phone numbers if any change.

Target Market(s)

Customers, suppliers, service providers

Contact Information for Business Card

Mavis Thorne
Tel: +44 (0) 208 473 2586
Fax: +44 (0) 208 473 5820
Email: mavis@pwlwoods.co.uk
Web: www.pwlwoods.co.uk

PWL Woods Ltd. 7 Falcon Court, Birchmore Way, Oakwick, Surrey CR4 6TJ, UNITED KINGDOM

IMPORTANT NOTICE - This message contains confidential information for the intended addressee only. Any views expressed are those of the sender not PWL Woods Ltd unless otherwise stated. If you receive this message [and any attachment(s)] in error you must not store, copy, disclose or otherwise use any part of it and should advise the sender immediately on 020 8473 9152. Internet communications are not guaranteed secure or virus free. PWL reserves the right to monitor all e-mail communications and does not accept responsibility for any loss or damage resulting from access of this e-mail or any file(s) attached.

Font styles to use
Sans Serif
Other font styles liked:
• not actually sure

Requirements
Must have
• mention of company's 40th Anniversary 1981-2021, which is the whole point of the design
Nice to have
• Our company colour is British Racing Green, but any green theme may be good
Maybe a tree design but allowing the company logo to stand out.

```html
<!DOCTYPE html>
<html lang="en">
<head>
<meta charset="utf-8">
<title>PWL Woods Ltd — 40th Anniversary Business Card</title>
<link rel="stylesheet" href="https://fonts.googleapis.com/css2?family=Archivo:wght@800&family=Arimo:wght@400;700&display=swap">
<style>
  :root {
    --page-bg: #e9e9e7;
    --card-white: #ffffff;
    --card-black: #1a1919;
    --card-black-hi: #2c2b2b;
    --ink: #151515;
    --ink-soft: #3a3a3a;
    --gold-dark: #b07a12;
    --gold: #e0a52a;
    --gold-light: #f5cf6a;
    --faint-mark: #2a2929;
  }
  * { box-sizing: border-box; margin: 0; padding: 0; }
  html, body {
    width: 1200px; height: 900px; overflow: hidden;
    background: var(--page-bg);
  }
  .sheet {
    position: relative; width: 1200px; height: 900px;
    display: flex; flex-direction: column; align-items: center; justify-content: center; gap: 40px;
  }
  .card {
    position: relative; width: 660px; height: 377px;
    border-radius: 26px; overflow: hidden;
    box-shadow: 0 10px 28px rgba(0,0,0,.18);
  }

  /* Back side */
  .card--back {
    background: linear-gradient(115deg, var(--card-black) 0%, var(--card-black) 55%, var(--card-black-hi) 72%, var(--card-black) 100%);
  }
  .card--back .faint-mark {
    position: absolute; left: -40px; top: 95px;
    width: 330px; height: 330px; border-radius: 50%;
    background: var(--faint-mark);
  }
  .wordmark {
    font-family: "Archivo", "Arial Black", sans-serif;
    font-weight: 800; letter-spacing: 2px; line-height: 1;
    display: flex; align-items: center; gap: 14px;
  }
  .wordmark .dot { border-radius: 50%; flex: none; }
  .card--back .wordmark {
    position: absolute; left: 285px; top: 130px;
    color: #ffffff; font-size: 64px;
  }
  .card--back .wordmark .dot { width: 46px; height: 46px; background: #ffffff; }

  /* Front side */
  .card--front { background: var(--card-white); }
  .anniversary-badge {
    position: absolute; right: 26px; top: 20px;
    width: 132px; height: 110px;
  }
  .anniversary-badge text { font-family: "Arimo", Arial, sans-serif; font-weight: 700; }
  .anniversary-badge .badge-number { font-family: "Archivo", "Arial Black", sans-serif; font-weight: 800; }
  .card--front .wordmark {
    position: absolute; left: 225px; top: 110px;
    color: var(--ink); font-size: 76px;
  }
  .card--front .wordmark .dot { width: 54px; height: 54px; background: var(--ink); }
  .holder-name {
    position: absolute; left: 62px; top: 276px;
    font-family: "Archivo", "Arial Black", sans-serif; font-weight: 800;
    font-size: 30px; letter-spacing: 1.5px; color: var(--ink);
    text-transform: uppercase;
  }
  .divider {
    position: absolute; left: 340px; top: 222px;
    width: 2px; height: 118px; background: var(--ink);
  }
  .contact-list {
    position: absolute; left: 362px; top: 222px;
    list-style: none;
    font-family: "Arimo", Arial, sans-serif; font-size: 20px; color: var(--ink-soft);
  }
  .contact-list li { display: flex; align-items: center; gap: 10px; height: 29px; }
  .contact-icon {
    width: 20px; height: 20px; border-radius: 4px; flex: none;
    background: linear-gradient(135deg, var(--gold-light), var(--gold) 50%, var(--gold-dark));
    display: flex; align-items: center; justify-content: center;
  }
  .contact-icon svg { width: 13px; height: 13px; }
</style>
</head>
<body>
<main class="sheet">

  <section class="card card--back" aria-label="Card back">
    <div class="faint-mark"></div>
    <div class="wordmark"><span class="dot"></span>PWL</div>
  </section>

  <section class="card card--front" aria-label="Card front">
    <svg class="anniversary-badge" role="img" aria-label="Gold 40th anniversary seal, 1981–2021" viewBox="0 0 132 110">
      <defs>
        <linearGradient id="seal-gold" x1="0" y1="0" x2="1" y2="1">
          <stop offset="0" stop-color="#f5cf6a"/>
          <stop offset=".5" stop-color="#e0a52a"/>
          <stop offset="1" stop-color="#b07a12"/>
        </linearGradient>
        <path id="seal-arc" d="M 30 50 A 36 36 0 0 1 102 50"/>
      </defs>
      <circle cx="66" cy="50" r="46" fill="url(#seal-gold)"/>
      <circle cx="66" cy="50" r="42" fill="#151515"/>
      <circle cx="66" cy="50" r="31" fill="none" stroke="url(#seal-gold)" stroke-width="1.5"/>
      <text font-size="9" fill="#f5cf6a" letter-spacing="1" text-anchor="middle">
        <textPath href="#seal-arc" startOffset="50%">1981-2021</textPath>
      </text>
      <text class="badge-number" x="66" y="62" font-size="34" fill="url(#seal-gold)" text-anchor="middle">40</text>
      <text x="91" y="38" font-size="8" fill="#f5cf6a" text-anchor="middle">TH</text>
      <path d="M6 66 L126 66 L120 74 L126 82 L6 82 L12 74 Z" fill="url(#seal-gold)"/>
      <text x="66" y="77.5" font-size="9" fill="#151515" letter-spacing="1.2" text-anchor="middle">ANNIVERSARY</text>
    </svg>

    <div class="wordmark"><span class="dot"></span>PWL</div>

    <h1 class="holder-name">Mavis Thorne</h1>
    <div class="divider"></div>

    <ul class="contact-list">
      <li>
        <span class="contact-icon"><svg viewBox="0 0 24 24"><path fill="#fff" d="M6.6 10.8a15.1 15.1 0 0 0 6.6 6.6l2.2-2.2c.3-.3.7-.4 1-.2 1.1.4 2.3.6 3.6.6.6 0 1 .4 1 1V20c0 .6-.4 1-1 1A17 17 0 0 1 3 4c0-.6.4-1 1-1h3.5c.6 0 1 .4 1 1 0 1.3.2 2.5.6 3.6.1.3 0 .7-.2 1z"/></svg></span>
        +44 (0) 208 473 2586
      </li>
      <li>
        <span class="contact-icon"><svg viewBox="0 0 24 24"><path fill="#fff" d="M6 3h10v5H6zM4 9h16a2 2 0 0 1 2 2v7h-4v3H6v-3H2v-7a2 2 0 0 1 2-2zm4 7v3h8v-3z"/></svg></span>
        +44 (0) 208 473 5820
      </li>
      <li>
        <span class="contact-icon"><svg viewBox="0 0 24 24"><path fill="#fff" d="M3 5h18v14H3zm2 2v.5l7 5 7-5V7zm0 3v7h14v-7l-7 5z"/></svg></span>
        mavis@pwlwoods.co.uk
      </li>
      <li>
        <span class="contact-icon"><svg viewBox="0 0 24 24"><circle cx="12" cy="12" r="9" fill="none" stroke="#fff" stroke-width="2"/><path d="M3 12h18M12 3c3 3 3 15 0 18M12 3c-3 3-3 15 0 18" fill="none" stroke="#fff" stroke-width="1.6"/></svg></span>
        www.pwlwoods.co.uk
      </li>
    </ul>
  </section>

</main>
</body>
</html>
```